Business card design Needed for new logo / Construction business, home extensions and new builds

We need a business card design using our new logo files which i will attach to this project :)

We are a small construction business specialising in home extensions, new builds and property development. We are very ambitious and would appreciate professional and elegant designs for our new business card.

Very serious about using the services on MakerQuarry and recently acquired our new logo from here :)

Please get involved, i will feedback when i can as i am very busy but can respond daily, thanks

Target Market(s)

People that want to build onto their houses, new building developments or adding too their existing property

Industry/Entity Type

Construction

Contact Information for Business Card

Renwick Tolliver Construction, Lionel Ashby (Managing Director), Tel 07822254961, email - info@renwick-tolliver, www.renwick-tolliver.co.uk

Colors

Designer to choose colors to be used in the design.

Requirements
Must have
• I like a deep grey on the back please. A lot of you have provided black from and back, try mixing things up a little. The black looks cool 😎 Thanks

```html
<!DOCTYPE html>
<html lang="en">
<head>
<meta charset="utf-8">
<title>Renwick Tolliver Construction – Business Card</title>
<link rel="stylesheet" href="https://fonts.googleapis.com/css2?family=Open+Sans:wght@400;600;700&display=swap">
<style>
  :root {
    --page: #2a2a2e;
    --card: #1f1f23;
    --card-back: #1b1b1f;
    --brand-back: #131316;
    --gold: #d9a02a;
    --gold-light: #f2c862;
    --gold-dark: #a8761a;
    --silver: #d8d8dc;
    --white: #f4f4f4;
  }
  * { box-sizing: border-box; margin: 0; padding: 0; }
  html, body {
    width: 1200px; height: 780px; overflow: hidden;
    background: var(--page);
    font-family: "Open Sans", Arial, sans-serif;
  }
  .canvas {
    width: 1200px; height: 780px;
    display: flex; flex-direction: column;
    align-items: center; justify-content: center; gap: 30px;
  }
  .card {
    position: relative;
    width: 600px; height: 343px;
    background: var(--card);
    overflow: hidden;
  }
  .card::after {
    content: "";
    position: absolute; left: 0; right: 0; bottom: 0; height: 3px;
    background: linear-gradient(90deg, var(--gold-dark), var(--gold-light) 45%, var(--gold) 70%, var(--gold-dark));
  }
  /* Back side */
  .card--back { background: var(--card-back); }
  .card--back .brand {
    position: absolute; inset: 0;
    display: flex; align-items: center; justify-content: center; gap: 14px;
    color: var(--brand-back);
  }
  .brand__mark {
    width: 14px; height: 14px; background: currentColor;
  }
  .brand__name {
    font-weight: 600; font-size: 22px; letter-spacing: 3px;
    text-transform: uppercase; line-height: 1.3; text-align: center;
  }
  /* Front side */
  .card--front .brand {
    position: absolute; left: 0; top: 0; width: 300px; height: 100%;
    display: flex; flex-direction: column; align-items: center; justify-content: center; gap: 14px;
    color: var(--gold);
  }
  .card--front .brand__name { font-size: 19px; }
  .divider {
    position: absolute; left: 300px; top: 78px; width: 1.5px; height: 186px;
    background: var(--white);
  }
  .details {
    position: absolute; left: 332px; top: 70px; right: 24px;
    color: var(--white);
  }
  .details__name { font-size: 26px; font-weight: 700; line-height: 1.1; }
  .details__first { color: var(--silver); }
  .details__last { color: var(--gold); }
  .details__role { font-size: 13px; margin-top: 2px; }
  .details__address { font-size: 13px; line-height: 1.45; margin-top: 16px; }
  .contact { list-style: none; margin-top: 14px; font-size: 13px; line-height: 1.55; }
  .contact li { display: flex; align-items: center; gap: 8px; }
  .contact svg { width: 12px; height: 12px; flex: none; }
</style>
</head>
<body>
<main class="canvas">
  <section class="card card--back" aria-label="Card back">
    <div class="brand">
      <span class="brand__mark"></span>
      <span class="brand__name">Renwick Tolliver<br>Construction</span>
    </div>
  </section>

  <section class="card card--front" aria-label="Card front">
    <div class="brand">
      <span class="brand__mark"></span>
      <span class="brand__name">Renwick Tolliver<br>Construction</span>
    </div>
    <div class="divider"></div>
    <div class="details">
      <h1 class="details__name"><span class="details__first">Lionel</span> <span class="details__last">Ashby</span></h1>
      <p class="details__role">Managing Director</p>
      <p class="details__address">Hatchley Road, Orlestone<br>Brackenmouth, BX4 7QN</p>
      <ul class="contact">
        <li>
          <svg viewBox="0 0 24 24" fill="var(--gold)"><path d="M6.6 10.8a15 15 0 0 0 6.6 6.6l2.2-2.2c.3-.3.7-.4 1-.2 1.1.4 2.3.6 3.6.6.6 0 1 .4 1 1V20c0 .6-.4 1-1 1A17 17 0 0 1 3 4c0-.6.4-1 1-1h3.5c.6 0 1 .4 1 1 0 1.3.2 2.5.6 3.6.1.3 0 .7-.2 1z"/></svg>
          <span>0782 225 4961</span>
        </li>
        <li>
          <svg viewBox="0 0 24 24" fill="none" stroke="var(--gold)" stroke-width="2.2"><rect x="3" y="5" width="18" height="14" rx="1"/><path d="M3 6l9 7 9-7"/></svg>
          <span>info@renwick-tolliver.co.uk</span>
        </li>
        <li>
          <svg viewBox="0 0 24 24" fill="none" stroke="var(--gold)" stroke-width="2.2"><circle cx="12" cy="12" r="9"/><path d="M3 12h18M12 3c3 3 3 15 0 18M12 3c-3 3-3 15 0 18"/></svg>
          <span>www.renwick-tolliver.co.uk</span>
        </li>
      </ul>
    </div>
  </section>
</main>
</body>
</html>
```